Vantro cards

I am in the auto motive, transportation business I would like a business card that is Something cool, modern edgy, having to do with car culture. I offer towing service for high and exotic cars. I also provide towing for collisions and car accidents. I offer open and enclosed transport nationwide.

Target Market(s)

Car culture people high end auto collectors

Industry/Entity Type

Towing car carrier

Contact Information for Business Card

My company colors black yellow and silver

Font styles to use
Serif

```html
<!DOCTYPE html>
<html lang="en">
<head>
<meta charset="UTF-8">
<title>Vantro Business Cards</title>
<link href="https://fonts.googleapis.com/css2?family=Poppins:wght@400;600;700&display=swap" rel="stylesheet">
<style>
  :root {
    --backdrop: #2a2a2a;
    --card: #0d0d0d;
    --yellow: #f4d84f;
    --silver: #c9c9c9;
    --white: #ffffff;
    --rule: #5a5a5a;
  }
  * { margin: 0; padding: 0; box-sizing: border-box; }
  html, body {
    width: 1200px; height: 900px; overflow: hidden;
    background: var(--backdrop);
    font-family: "Poppins", sans-serif;
  }
  .canvas {
    width: 1200px; height: 900px;
    display: flex; flex-direction: column;
    align-items: center; justify-content: center; gap: 40px;
  }
  .card {
    width: 700px; height: 400px;
    background: var(--card);
    border-radius: 4px;
    box-shadow: 0 10px 30px rgba(0,0,0,.5);
    position: relative;
  }
  .card-front { display: flex; align-items: center; }
  .brand-block {
    width: 330px; height: 100%;
    display: flex; align-items: center; justify-content: center;
  }
  .brand-name {
    font-weight: 700; font-size: 56px; letter-spacing: 2px;
    color: var(--white); text-transform: uppercase;
    display: flex; align-items: center; gap: 14px;
  }
  .brand-mark {
    width: 18px; height: 18px; background: var(--yellow);
  }
  .divider {
    width: 1px; height: 200px; background: var(--rule);
  }
  .contact-block { padding-left: 34px; }
  .person-name {
    color: var(--yellow); font-weight: 700; font-size: 26px;
    text-transform: uppercase; line-height: 1.1;
  }
  .person-role {
    color: var(--silver); font-size: 17px; margin-bottom: 18px;
  }
  .contact-line {
    display: flex; align-items: center; gap: 10px;
    color: var(--silver); font-size: 17px; line-height: 1.6;
  }
  .contact-line svg { width: 16px; height: 16px; flex: none; }
  .address {
    color: var(--silver); font-size: 17px; line-height: 1.4;
    margin-top: 16px; padding-left: 26px;
  }
  .card-back { display: flex; align-items: center; justify-content: center; }
  .card-back .brand-name { font-size: 72px; }
  .card-back .brand-mark { width: 24px; height: 24px; }
</style>
</head>
<body>
<main class="canvas">
  <section class="card card-front">
    <div class="brand-block">
      <div class="brand-name"><span class="brand-mark"></span>Vantro</div>
    </div>
    <div class="divider"></div>
    <div class="contact-block">
      <p class="person-name">Marcus Hale</p>
      <p class="person-role">Managing Director</p>
      <p class="contact-line">
        <svg viewBox="0 0 24 24" fill="var(--yellow)"><path d="M6.6 10.8a15 15 0 0 0 6.6 6.6l2.2-2.2a1 1 0 0 1 1-.25 11.4 11.4 0 0 0 3.6.57 1 1 0 0 1 1 1V20a1 1 0 0 1-1 1A17 17 0 0 1 3 4a1 1 0 0 1 1-1h3.5a1 1 0 0 1 1 1c0 1.25.2 2.45.57 3.57a1 1 0 0 1-.25 1z"/></svg>
        055-987 210 436
      </p>
      <p class="contact-line">
        <svg viewBox="0 0 24 24" fill="var(--yellow)"><path d="M2 5h20v14H2z M2 5l10 8 10-8" stroke="var(--card)" stroke-width="1.5"/></svg>
        hello@vantrotow.com
      </p>
      <p class="contact-line">
        <svg viewBox="0 0 24 24" fill="none" stroke="var(--yellow)" stroke-width="2"><circle cx="12" cy="12" r="9"/><path d="M3 12h18M12 3c3 3 3 15 0 18M12 3c-3 3-3 15 0 18"/></svg>
        www.vantrotow.com
      </p>
      <p class="address">318, Carrier Road East<br>60714, Springfield</p>
    </div>
  </section>

  <section class="card card-back">
    <div class="brand-name"><span class="brand-mark"></span>Vantro</div>
  </section>
</main>
</body>
</html>
```